Tri-Fold Brochure for Christian Author and Speaker

Lorna Whitfield is an inspirational author and speaker, sharing her testimony and encouraging others in their walk with Christ. A gifted writer, her work has been featured on Gently Radiant, Steadfast Mornings, and Hymns & Teacups Magazine (Fall 2011).

Lorna ‘s first book, Leaving the Lantern Room: Unmasking Hidden Snares in Ordinary Living, is an informative memoir and Bible study, recounting her journey from committed Christian to witch, medium, and ghost hunter for eight years until restored to faith in Jesus Christ. She was a contributing author to Walking Past the Shadows: A Candid View of Sorcery from Those Who Left by Dale Pennington and a consultant for the novel The Keeper of Marlow Hollow by Beacon Prize Winning Author, Helen Osgood.

Lorna’s second book, An Insider’s Guide to Spiritual Warfare: 20 Battle-Tested Strategies from Behind Enemy Lines, will be published by Harvest Lane Press for Fall 2014.

Lorna is a wife and mother. She enjoys writing, spending time with her family, taking long walks, listening to music of all kinds, and experiencing God’s daily gift called life.

You can read more about Lorna and see the look and feel we are going for at www.lornawhitfield.example

The brochure is to be used as a promotional tool to gain Lorna speaking engagements. You can see the topics she covers at http://www.lornawhitfield.example/speaking-engagements/.

More info can be found at: https://www.facebook.com/AuthorLornaWhitfield
https://www.facebook.com/VMUCX
https://www.facebook.com/LeavingtheLanternRoom
https://www.facebook.com/OpenDoorOutreach
http://www.opendooroutreach.example

I have uploaded 3 headshots, book covers for both of Lorna's books and the design layout in .EPS format from Swiftprintery.example where I will be getting printing done.

3 more days till the contest ends get your final designs in.

Reason: I'm extending this as I am tied up at a leadership conference and will not be able to give this the attention it deserves till the weekend.

Target Market(s)

Churches and women's groups. Lorna's current audience skews heavy to women on a 70/30 ratio.

Industry/Entity Type

Christian

Requirements
Must have
• Headshot I have uploaded 3
Quotes from previous speaking engagements you can find those at http://www.lornawhitfield.example/speaking-engagements/

```html
<!DOCTYPE html>
<html lang="en">
<head>
<meta charset="utf-8">
<title>Lorna Whitfield – Tri-Fold Brochure</title>
<link href="https://fonts.googleapis.com/css2?family=Cinzel:wght@400;600&family=Didact+Gothic&family=Poppins:wght@500;600;700&display=swap" rel="stylesheet">
<style>
  :root{
    --berry:#ad1457;
    --berry-dark:#86103f;
    --blush:#f8e8ec;
    --blush-deep:#f0d3dc;
    --paper:#fffafb;
    --ink:#6d5a63;
    --stage:#e7e3e5;
    --photo-a:#8a6a5c;
    --photo-b:#3f5a3a;
  }
  *{box-sizing:border-box;margin:0;padding:0}
  html,body{width:676px;height:1200px;overflow:hidden;background:var(--stage)}
  body{font-family:"Didact Gothic",sans-serif;color:var(--ink)}
  .canvas{position:relative;width:676px;height:1200px}
  .spread{position:absolute;left:20px;width:636px;height:491px;display:flex;box-shadow:0 4px 14px rgba(60,20,35,.18)}
  .spread--outside{top:89px}
  .spread--inside{top:620px}
  .panel{position:relative;width:212px;height:491px;overflow:hidden}
  .photo{background:linear-gradient(160deg,var(--photo-a),#c79a86 55%,var(--photo-b))}

  /* Speaking panel */
  .panel--speaking{background:linear-gradient(180deg,var(--paper),var(--blush))}
  .speaking__tab{position:absolute;left:0;top:18px;background:var(--berry);color:#fff;font-family:"Poppins",sans-serif;font-weight:600;font-size:15px;padding:6px 16px 6px 12px;border-radius:0 18px 18px 0}
  .speaking__body{position:absolute;left:12px;right:12px;top:56px;font-size:8.6px;line-height:1.5;text-align:justify}
  .speaking__body b{color:var(--berry)}
  .topics__title{margin-top:12px;font-family:"Poppins",sans-serif;font-weight:600;color:var(--berry);font-size:9.5px}
  .topics{list-style:none;margin-top:4px}
  .topics li{font-size:8.8px;line-height:1.6;color:var(--berry-dark);padding-left:11px;position:relative}
  .topics li::before{content:"";position:absolute;left:0;top:4px;width:6px;height:6px;background:var(--berry)}
  .speaking__photo{position:absolute;left:0;bottom:0;width:212px;height:150px}

  /* Testimony panel */
  .panel--testimony{background:var(--berry);color:#fff;text-align:center}
  .testimony__title{font-family:"Poppins",sans-serif;font-weight:600;font-size:15px;margin-top:20px}
  .testimony__text{margin:8px 16px 0;font-size:9.2px;line-height:1.55;text-align:justify}
  .testimony__frame{width:82px;height:100px;margin:18px auto 0;border:3px solid #fff}
  .testimony__name{font-family:"Cinzel",serif;font-size:12px;line-height:1.05;margin-top:8px;letter-spacing:.5px}
  .testimony__url{font-size:8.4px;margin-top:3px}

  /* Cover panel */
  .panel--cover{background:linear-gradient(180deg,var(--paper),var(--blush) 70%,var(--paper))}
  .cover__name{position:absolute;left:14px;top:18px;font-family:"Cinzel",serif;color:var(--berry);font-size:22px;line-height:.98;letter-spacing:.5px}
  .cover__role{font-family:"Cinzel",serif;color:var(--berry-dark);font-size:10px;letter-spacing:1px;margin-top:4px}
  .cover__art{position:absolute;left:0;top:80px}
  .cover__tagline{position:absolute;right:14px;top:340px;text-align:right;font-family:"Poppins",sans-serif;color:var(--berry-dark);line-height:1.05}
  .cover__tagline .lead{font-weight:700;font-size:15px}
  .cover__tagline .soft{font-weight:500;font-size:12px;color:var(--berry)}
  .cover__tagline .strong{font-weight:700;font-size:15px}

  /* Inside spread */
  .spread--inside{background:linear-gradient(180deg,var(--paper),var(--blush) 60%,var(--paper))}
  .band{position:absolute;left:0;width:636px;height:14px;background:var(--berry)}
  .band--top{top:0}
  .band--bottom{bottom:0}
  .notch{position:absolute;width:36px;height:10px;background:var(--paper);border-radius:6px}
  .band--top .notch{bottom:-2px}
  .band--bottom .notch{top:-2px}
  .inside-tab{position:absolute;left:14px;top:0;background:var(--berry);color:#fff;font-family:"Cinzel",serif;font-size:10.5px;padding:5px 12px 6px;border-radius:0 0 10px 10px;z-index:2}
  .panel--quotes{padding:36px 14px 20px;border-right:1px dashed rgba(173,20,87,.18)}
  .panel--quotes:last-child{border-right:0}
  .panel--quotes.first{padding-top:40px}
  .question{font-family:"Poppins",sans-serif;font-weight:600;color:var(--berry);font-size:11px;line-height:1.2}
  .source{font-family:"Poppins",sans-serif;font-weight:700;color:var(--berry-dark);font-size:11px;line-height:1.15;margin:8px 0 5px;text-align:center}
  .source small{font-weight:500;font-size:9.5px;display:block}
  .quote{font-size:8.5px;line-height:1.5;text-align:justify}
  .quote b{color:var(--berry);font-weight:normal}
  .quotes__photo{height:120px;margin:8px -14px 4px;border-top:4px solid var(--berry);border-bottom:4px solid var(--berry)}
  .panel--quotes.third{padding-top:20px}
</style>
</head>
<body>
<div class="canvas">

  <section class="spread spread--outside">
    <article class="panel panel--speaking">
      <h2 class="speaking__tab">Speaking</h2>
      <div class="speaking__body">
        <p><b>Lorna Whitfield</b> shares from her own life lessons and as a Biblical Counselor, encouraging others toward a deeper walk with God. Lorna offers sound, heartfelt and practical biblical advice on issues relevant to the 21st Century Christian. Read more…</p>
        <h3 class="topics__title">Speaking Topics Include:</h3>
        <ul class="topics">
          <li>Christians and the Occult</li>
          <li>Homelessness (with Rowan Whitfield)</li>
          <li>Human Trafficking</li>
          <li>Marriage Restoration (with Rowan Whitfield)</li>
          <li>Prayer as a Lifestyle</li>
          <li>Spiritual Warfare</li>
        </ul>
      </div>
      <svg class="speaking__photo" viewBox="0 0 212 150" role="img" aria-label="Headshot of Lorna Whitfield">
        <defs><linearGradient id="spk" x1="0" y1="0" x2="1" y2="1"><stop offset="0" stop-color="#a9746a"/><stop offset=".6" stop-color="#6e3d3a"/><stop offset="1" stop-color="#3b2a2a"/></linearGradient></defs>
        <path d="M0 22 Q106 -6 212 18 V150 H0 Z" fill="url(#spk)"/>
        <path d="M0 22 Q106 -6 212 18" fill="none" stroke="#ad1457" stroke-width="4"/>
      </svg>
    </article>

    <article class="panel panel--testimony">
      <h2 class="testimony__title">Testimony</h2>
      <p class="testimony__text">I was raised in a traditional <b>Christian home</b>. One of my earliest memories of church is sitting on a hard wooden pew with my mother listening to a pipe organ play a traditional hymn. We were attending a Methodist church at the time. I remember hearing Bible stories, singing songs about the B.I.B.L.E. and Jesus Loving the Little Children. It wasn't until I was six years old attending Vacation Bible School that I learned how Jesus wanted to save me from my sins. Read more…</p>
      <div class="testimony__frame photo" role="img" aria-label="Portrait of Lorna Whitfield"></div>
      <p class="testimony__name">LORNA<br>WHITFIELD</p>
      <p class="testimony__url">www.lornawhitfield.example</p>
    </article>

    <article class="panel panel--cover">
      <h1 class="cover__name">LORNA<br>WHITFIELD<span class="cover__role" style="display:block">AUTHOR | SPEAKER</span></h1>
      <svg class="cover__art" width="212" height="230" viewBox="0 0 212 230" role="img" aria-label="Outdoor portrait of Lorna Whitfield in a garden">
        <defs><linearGradient id="cov" x1="0" y1="0" x2="1" y2="1"><stop offset="0" stop-color="#5b7040"/><stop offset=".45" stop-color="#9c7a68"/><stop offset="1" stop-color="#4d3a33"/></linearGradient></defs>
        <path d="M0 8 Q120 -10 212 6 V170 Q110 240 0 200 Z" fill="url(#cov)"/>
        <path d="M0 206 Q110 248 212 174" fill="none" stroke="#ad1457" stroke-width="6"/>
        <path d="M0 216 Q110 254 212 186" fill="none" stroke="#f0d3dc" stroke-width="3"/>
      </svg>
      <p class="cover__tagline">
        <span class="lead">Lorna Whitfield</span><br>
        <span class="soft">is an </span><span class="strong">Inspirational</span><br>
        <span class="strong">Author</span> <span class="soft">and</span> <span class="strong">Speaker</span>
      </p>
    </article>
  </section>

  <section class="spread spread--inside">
    <div class="band band--top"><span class="notch" style="left:160px"></span><span class="notch" style="left:400px"></span><span class="notch" style="left:590px"></span></div>
    <div class="band band--bottom"><span class="notch" style="left:20px"></span><span class="notch" style="left:250px"></span><span class="notch" style="left:460px"></span></div>
    <span class="inside-tab">AUTHOR &amp; SPEAKER</span>

    <article class="panel panel--quotes first">
      <h2 class="question">What's Lorna Like as a Speaker?</h2>
      <h3 class="source">Marian Holcombe, Eastbrook Community <small>Church Women's Ministry</small></h3>
      <p class="quote">The Women's Ministry at Eastbrook Community Church in Ashford, MI invited <b>Lorna Whitfield</b> to speak at our Mother or Daughter Banquet earlier this month. I am so glad she accepted! We couldn't have chosen a speaker to fit in better than <b>Lorna</b>. She took our theme, "Instruments", and incorporated that into her speaking time with us. She used life examples and spoke directly into the hearts of the women and girls that attended our banquet. She even took time to speak to my teen aged daughters after the Read more....</p>
    </article>

    <article class="panel panel--quotes">
      <h3 class="source" style="margin-top:-10px">Grant Albrecht, Harmony Crossing Seminar Tent, <small>Coordinator</small></h3>
      <p class="quote">"I was honored and delighted to have <b>Lorna Whitfield</b> be one of our speakers in the "Harmony Crossing Seminar Tent" at Harmony Christian Music Festival in Lakeport, Michigan (one of the nation's top 10 Christian music festivals). <b>Lorna</b> has a unique testimony and style of speaking that keeps people, young and old, engaged into the heart of her message. Her stories of involvement in the occult and her conclusion of how God rescued her from these traps, answers many of the questions that people often have, read more....</p>
      <h3 class="source">Joan Meyers, Living Vine Church, <small>Women's Christmas Tea Coordinator</small></h3>
      <p class="quote">"We had <b>Lorna</b> speak at our Women's Tea. Even though the weather was terrible in Northern Michigan we had a good turnout</p>
    </article>

    <article class="panel panel--quotes third">
      <p class="quote">and I had several women tell me afterwards how blessed they were with <b>Lorna's</b> message. The emphasis was on putting Christ first during the holidays and read more....</p>
      <div class="quotes__photo photo" role="img" aria-label="Smiling headshot of Lorna Whitfield"></div>
      <h3 class="source">Dirk Vandermolen, Pastor, Cornerstone Reformed <small>Church</small></h3>
      <p class="quote">"<b>Lorna Whitfield</b> spoke at our church sharing with us her testimony which includes how she attempted to blend witchcraft with Christianity. Obviously, she discovered that there is no compromising of the Gospel and the Holy Spirit brought her back in an amazing way. Read more....</p>
    </article>
  </section>

</div>
</body>
</html>
```